Creation of a Velmaro website

Velmaro is a company% 26 # 233; t% 26 # 233; consulting that accompanies Swiss companies or% 26 # 233; strang% 26 # 232; res in the d% 26 # 233; development of their business on the market% 26 # 233; Switzerland by providing strategic contacts (personalized contact program% 26 # 233; s) or market information% 26 # 233; (% 26 # 233; market research% 26 # 233;) and by providing administrative support (repr% 26 # 233; tax representation) or logistics (organization of% 26 # 233; v% 26 # 233; nement, assistance for participation% 26 # 224; fairs). Our customers are mainly European companies wishing to develop their business in Switzerland. N% 26 # 233; however, our services are% 26 # 233; also aimed at Swiss companies wishing to develop in other parts of Switzerland. Our site must therefore be% 26 # 234; capable of being translated into several languages. The services offered% 26 # 233; s by Velmaro may also% 26 # 233; also% 26 # 39;% 26 # 233; tender% 26 # 224; promoting tourism in Switzerland for countries or regions% 26 # 233; foreigners or% 26 # 224; the promotion of trade fairs or fairs with% 26 # 232; sd% 26 # 39; companies of the sectors concerned% 26 # 233; s. It is therefore n% 26 # 233; necessary to be able to add sub-headings of services which can% 26 # 234; be displayed% 26 # 233; es or hide% 26 # 233; es as required. We are 2 associates% 26 # 233; s, low% 26 # 233; s in the French-speaking parts (Neuch% 26 # 226; tel) and al% 26 # 233; manique (Zurich) of Switzerland.

Target Market(s)

Swiss or European companies wishing to develop their activities in Switzerland.

Coding

Coded - Design and coding required

Colors

Designer to choose colors to be used in the design.

Requirements
Must have
• A home page A section of% 26 # 233; writing the services offered% 26 # 233; es by Velmaro with the possibility% 26 # 233; d% 26 # 39; add sub-headings which can% 26 # 234; be displayed% 26 # 233; e or hidden% 26 # 233; e A page with the r% 26 # 233; f% 26 # 233; which can be displayed% 26 # 233; e or hidden% 26 # 233; e A page of% 26 # 233; writing l% 26 # 39;% 26 # 233; team A page with form contact, addresses and int card% 26 # 233; gr% 26 # 233; e The site must% 26 # 234; be low% 26 # 233; on a CMS allowing% 26 # 39;% 26 # 234; to be autonomous in modifying the website The possibility% 26 # 233; to be able to translate the site into several languages (FR, EN, DE, IT, NL, ...)

```html
<!DOCTYPE html>
<html lang="en">
<head>
<meta charset="utf-8">
<title>Velmaro</title>
<link rel="stylesheet" href="https://fonts.googleapis.com/css2?family=Michroma&family=Mulish:wght@400;600;700&display=swap">
<style>
:root{
  --navy:#1e3a52;
  --navy-deep:#152a3c;
  --navy-mid:#2e5870;
  --ink:#2b2f36;
  --muted:#7b8088;
  --sky:#e6f1fb;
  --mist:#e9eaee;
  --paper:#ffffff;
  --soft:#f9f9fa;
  --line:#cfd3d9;
  --button-light:#b6c2d1;
}
*{box-sizing:border-box;margin:0;padding:0}
html,body{width:1200px;height:3179px;overflow:hidden;background:var(--paper)}
body{position:relative;font-family:"Mulish",sans-serif;color:var(--ink)}
.abs{position:absolute}
.display{font-family:"Michroma",sans-serif;letter-spacing:0;white-space:nowrap}
.bg-circle{position:absolute;border-radius:50%;background:var(--sky)}

/* header */
.brand{left:144px;top:31px;display:flex;align-items:center;gap:22px}
.brand-mark{width:41px;height:41px;border-radius:9px;background:var(--navy)}
.brand-name{font-family:"Mulish",sans-serif;font-weight:400;font-size:34px;letter-spacing:4px;color:var(--navy)}
.nav{left:515px;top:44px;display:flex;gap:25px;font-size:14px;color:var(--ink)}
.nav a{color:inherit;text-decoration:none;position:relative}
.nav a.active::after{content:"";position:absolute;left:-4px;right:-4px;top:22px;height:2px;background:var(--navy)}
.lang{left:926px;top:43px;display:flex;align-items:center;gap:8px;font-size:14px}
.lang-dot{width:20px;height:20px;border-radius:50%;background:#c8102e}
.lang-caret{width:0;height:0;border-left:5px solid transparent;border-right:5px solid transparent;border-top:6px solid var(--ink)}

/* hero */
.hero-title{left:141px;top:228px;font-size:46px;line-height:60px;color:var(--navy)}
.hero-sub{left:143px;top:328px;width:420px;font-size:18px;line-height:27px;color:var(--ink)}
.btn{display:flex;align-items:center;justify-content:center;background:var(--navy);color:#fff;font-size:15px;border-radius:4px}
.hero-btn{left:143px;top:420px;width:149px;height:44px}
.dots{left:143px;top:523px;display:flex;gap:7px}
.dots span{width:8px;height:8px;border-radius:50%;background:var(--line)}
.dots span.on{background:var(--navy)}
.hero-photo{left:580px;top:116px;width:475px;height:477px;border-radius:130px;background:linear-gradient(180deg,#6f97ab 0%,#a9c4d1 35%,#5c7a8c 70%,#2c4a62 100%)}

/* about */
.about-art{left:93px;top:728px;width:525px;height:425px;border-radius:45% 55% 40% 60%/50% 45% 55% 50%;background:var(--mist)}
.about-title{left:678px;top:788px;font-size:30px;line-height:40px;color:var(--navy)}
.about-title .lite{color:var(--ink)}
.about-text{left:678px;top:858px;width:380px;font-size:13.5px;line-height:27px;color:var(--muted)}
.about-text p+p{margin-top:14px}
.about-btn{left:678px;top:1094px;width:149px;height:44px}

/* services */
.arc{left:0;top:1285px}
.section-title{width:1200px;left:0;text-align:center;font-size:30px;line-height:40px;color:var(--navy)}
.section-title .lite{color:var(--ink)}
.service{display:flex;flex-direction:column;align-items:center;text-align:center;color:#fff;border-radius:72px;background:linear-gradient(180deg,var(--navy-mid),var(--navy-deep));padding:24px 26px 0}
.service h3{font-size:22px;font-weight:700;letter-spacing:.5px;margin:14px 0 16px}
.service p{font-size:12px;line-height:21px}
.service svg{stroke:#fff;fill:none;stroke-width:2}
.service.featured{border-radius:86px;box-shadow:inset 0 0 0 2px rgba(255,255,255,.15),0 8px 20px rgba(21,42,60,.25);padding:34px 46px 0}
.service.featured h3{font-size:25px;line-height:34px}
.service.featured p{font-size:13px;line-height:22px}

/* news */
.news-band{left:0;top:1969px;width:1200px;height:462px;background:var(--soft)}
.news-card{width:277px;height:186px;background:#fff;border:1.5px solid var(--line);padding:20px 22px}
.news-card.raised{box-shadow:0 4px 14px rgba(0,0,0,.08)}
.news-head{display:flex;gap:12px}
.date{width:48px;height:46px;flex:none;background:var(--navy);color:#fff;text-align:center;font-weight:700;font-size:19px;line-height:22px;padding-top:4px}
.date small{display:block;font-size:11px;font-weight:400;line-height:13px}
.news-head h4{font-size:15px;line-height:22px;font-weight:700;color:var(--ink)}
.news-card p{margin-top:14px;font-size:11px;line-height:19px;color:var(--muted)}
.news-card a{display:block;margin-top:10px;font-size:13px;font-weight:700;color:var(--navy);text-decoration:none}
.chev{top:2206px}

/* contact */
.contact-band{left:0;top:2431px;width:1200px;height:748px;background:var(--navy)}
.contact-title{color:#fff;font-size:31px}
.info{display:flex;align-items:center;gap:12px;color:#fff;font-size:13px;line-height:17px}
.info-dot{width:40px;height:40px;border-radius:50%;background:#c2cbd6;display:flex;align-items:center;justify-content:center;flex:none}
.field{background:#fff;font-size:13px;color:var(--muted);padding:0 22px;display:flex;align-items:center;height:43px;width:277px}
.field.message{width:855px;height:98px;align-items:flex-start;padding-top:16px}
.submit{left:506px;top:2894px;width:188px;height:44px;background:var(--button-light);color:var(--navy);font-size:14px;display:flex;align-items:center;justify-content:center;border-radius:3px}
.footer-arc{left:0;top:3010px}
.social{left:551px;top:3071px;display:flex;gap:7px}
.social span{width:28px;height:28px;border-radius:50%}
.copy{left:0;width:1200px;top:3122px;text-align:center;font-size:13px;color:var(--navy)}
</style>
</head>
<body>

<div class="bg-circle" style="left:-445px;top:24px;width:544px;height:544px"></div>
<div class="bg-circle" style="left:803px;top:0;width:418px;height:613px;border-radius:0 0 50% 50%/0 0 48% 48%"></div>

<header>
  <div class="abs brand"><span class="brand-mark"></span><span class="brand-name">VELMARO</span></div>
  <nav class="abs nav">
    <a class="active">Home</a><a>About us</a><a>Services</a><a>News</a><a>Contact</a>
  </nav>
  <div class="abs lang"><span class="lang-dot"></span>EN<span class="lang-caret"></span></div>
</header>

<section class="hero">
  <h1 class="abs display hero-title">VELMARO</h1>
  <p class="abs hero-sub">Sed ut perspiciatis unde omndoloremque lauum iste natuserrorluptatem accusantium</p>
  <a class="abs btn hero-btn">GET STARTED</a>
  <div class="abs dots"><span></span><span></span><span class="on"></span><span></span><span></span></div>
  <div class="abs hero-photo" role="img" aria-label="Photo of a businessman climbing a bright staircase, framed in a rounded square"></div>
</section>

<section class="about">
  <div class="abs about-art" role="img" aria-label="Illustration of a presenter pointing to a bar chart on an easel"></div>
  <h2 class="abs display about-title"><span class="lite">ABOUT</span> VELMARO</h2>
  <div class="abs about-text">
    <p>Lorem ipsum dolor sit amet, consectetur adipiscing elit, sed do eiusmod tempor incididunt ut labore et dolore magna aliquas ipsum suspendisse ultrices grarem ipsum dolor sit amet, consectetur adipiscing elit.</p>
    <p>Sed do eiusmod tempor incididunt ut labore et doloruas ipsum suspendisse ultrices gravidisus commodo viverra maecenas mmodo vivccumsan lacus vel facilisis.</p>
  </div>
  <a class="abs btn about-btn">READ MORE</a>
</section>

<section class="services">
  <svg class="abs arc" width="1200" height="200" viewBox="0 0 1200 200"><path d="M0 185 Q600 -120 1200 185" fill="none" stroke="#f1f2f4" stroke-width="3"/></svg>
  <h2 class="abs display section-title" style="top:1390px"><span class="lite">WHAT</span> WE DO</h2>

  <div class="abs service" style="left:144px;top:1531px;width:254px;height:255px">
    <svg width="64" height="64" viewBox="0 0 64 64"><rect x="14" y="6" width="38" height="52" rx="3"/><circle cx="26" cy="22" r="10"/><path d="M26 12v10h10M20 46l8-8 6 6 10-10M38 18h8M38 24h8"/></svg>
    <h3>RESEARCH</h3>
    <p>Lorem ipsum dolor sit consectetur adipiscing elit, sed do eiusmod tempor incididuntt labore</p>
  </div>

  <div class="abs service featured" style="left:440px;top:1546px;width:322px;height:325px">
    <svg width="70" height="76" viewBox="0 0 70 76"><rect x="14" y="4" width="40" height="66" rx="3"/><path d="M22 16h22M22 24h22M22 32h22M22 40h16M22 58l4-4 4 4 4-4 4 4 4-4"/><circle cx="56" cy="24" r="9"/><path d="M56 19v10"/></svg>
    <h3>TAX<br>REPRESENTATION</h3>
    <p>Lorem ipsum dolor sit consectetur adipiscing elit, sed do eiusmod tempor incididuntt labore</p>
  </div>

  <div class="abs service" style="left:800px;top:1531px;width:254px;height:255px">
    <svg width="76" height="60" viewBox="0 0 76 60"><rect x="4" y="10" width="44" height="34"/><path d="M48 22h14l10 12v10H48z"/><circle cx="18" cy="46" r="6"/><circle cx="60" cy="46" r="6"/></svg>
    <h3>LOGISTICS</h3>
    <p>Lorem ipsum dolor sit consectetur adipiscing elit, sed do eiusmod tempor incididuntt labore</p>
  </div>
</section>

<section class="news">
  <div class="abs news-band"></div>
  <h2 class="abs display section-title" style="top:2048px"><span class="lite">LATEST</span> NEWS</h2>

  <svg class="abs chev" style="left:55px" width="34" height="66" viewBox="0 0 34 66"><path d="M32 2L2 33l30 31" fill="none" stroke="#9aa1aa" stroke-width="1.5"/></svg>
  <svg class="abs chev" style="left:1111px" width="34" height="66" viewBox="0 0 34 66"><path d="M2 2l30 31L2 64" fill="none" stroke="#9aa1aa" stroke-width="1.5"/></svg>

  <article class="abs news-card" style="left:156px;top:2146px">
    <div class="news-head"><div class="date">02<small>JAN</small></div><h4>Pellentesque faucibus Ut accumsan ultric</h4></div>
    <p>Duis quam Nam eget lacus Aliquam erat volutpat Quisque dignissim congue leovel lacus vitae felis vestibulum</p>
    <a>READ MORE</a>
  </article>
  <article class="abs news-card raised" style="left:462px;top:2146px">
    <div class="news-head"><div class="date">02<small>JAN</small></div><h4>Pellentesque faucibus Ut accumsan ultric</h4></div>
    <p>Duis quam Nam eget lacus Aliquam erat volutpat Quisque dignissim congue leovel lacus vitae felis vestibulum</p>
    <a>READ MORE</a>
  </article>
  <article class="abs news-card" style="left:768px;top:2146px">
    <div class="news-head"><div class="date">02<small>JAN</small></div><h4>Pellentesque faucibus Ut accumsan ultric</h4></div>
    <p>Duis quam Nam eget lacus Aliquam erat volutpat Quisque dignissim congue leovel lacus vitae felis vestibulum</p>
    <a>READ MORE</a>
  </article>
</section>

<section class="contact">
  <div class="abs contact-band"></div>
  <h2 class="abs display section-title contact-title" style="top:2517px">CONTACT FORM</h2>

  <div class="abs info" style="left:284px;top:2617px">
    <span class="info-dot"><svg width="12" height="16" viewBox="0 0 12 16"><path d="M6 15s5-6 5-9A5 5 0 0 0 1 6c0 3 5 9 5 9z" fill="#fff"/><circle cx="6" cy="6" r="2" fill="#c2cbd6"/></svg></span>
    <span>1232,Lorem ipsum doloram<br>etnsectetur adiscing,</span>
  </div>
  <div class="abs info" style="left:537px;top:2617px">
    <span class="info-dot"><svg width="14" height="14" viewBox="0 0 14 14"><path d="M3 1l3 3-2 2a8 8 0 0 0 4 4l2-2 3 3-2 2C6 13 1 8 1 3z" fill="#fff"/></svg></span>
    <span>1 555 014 2290</span>
  </div>
  <div class="abs info" style="left:717px;top:2617px">
    <span class="info-dot"><svg width="14" height="10" viewBox="0 0 14 10"><rect width="14" height="10" rx="1" fill="#fff"/><path d="M1 1l6 5 6-5" fill="none" stroke="#c2cbd6" stroke-width="1.4"/></svg></span>
    <span>Email : info@velmaro.com</span>
  </div>

  <div class="abs field" style="left:172px;top:2709px">Enter Name</div>
  <div class="abs field" style="left:462px;top:2709px">Enter Email</div>
  <div class="abs field" style="left:751px;top:2709px">Enter Phone</div>
  <div class="abs field message" style="left:172px;top:2765px">Message</div>
  <div class="abs submit">SUBMIT MESSAGE</div>
</section>

<footer>
  <svg class="abs footer-arc" width="1200" height="169" viewBox="0 0 1200 169"><path d="M0 169 Q600 -150 1200 169 Z" fill="#fff"/></svg>
  <div class="abs social">
    <span style="background:#3b5998"></span><span style="background:#1da1f2"></span><span style="background:var(--navy)"></span>
  </div>
  <p class="abs copy">Copyright 2020 Velmaro.All Rights Reserved &nbsp;|&nbsp; Privacy Policy</p>
</footer>

</body>
</html>
```